Business Card Design Project

Actor, Producer, Vocal Coach, Choral Director, Song WriterPhone: (215) 555-0142 Fax: (215) 856-3933Email: waltierblocker@gmail.comFacebook: facebook.com/waltier.blockerTwitter: @thedf482

Industry/Entity Type

Business

Contact Information for Business Card

Business Cards that include my picture

Colors

Designer to choose colors to be used in the design.

```html
<!DOCTYPE html>
<html lang="en">
<head>
<meta charset="utf-8">
<title>Dorian Fellsmore — Business Card</title>
<link href="https://fonts.googleapis.com/css2?family=Didact+Gothic&display=swap" rel="stylesheet">
<style>
  :root {
    --ink: #0a0b0d;
    --pink: #ec2a84;
    --paper: #ffffff;
    --backdrop: #ece7df;
    --photo-light: #dcdad6;
    --photo-dark: #a9a6a2;
    --text: #151515;
  }
  html, body {
    margin: 0;
    width: 1189px;
    height: 1200px;
    overflow: hidden;
    background: var(--backdrop);
  }
  .canvas {
    position: relative;
    width: 1189px;
    height: 1200px;
  }
  .card {
    position: absolute;
    left: 274px;
    top: 40px;
    width: 583px;
    height: 1020px;
    transform: scale(1.098);
    transform-origin: top left;
    overflow: hidden;
    font-family: "Didact Gothic", "Century Gothic", sans-serif;
    color: var(--text);
    box-shadow: 0 10px 30px rgba(0,0,0,0.18);
  }
  .card-shapes {
    position: absolute;
    inset: 0;
  }
  .holder-name {
    position: absolute;
    left: 53px;
    top: 498px;
    margin: 0;
    font-size: 45px;
    font-weight: 400;
    letter-spacing: 0.5px;
    white-space: nowrap;
  }
  .roles {
    position: absolute;
    left: 53px;
    top: 588px;
    margin: 0;
    font-size: 24px;
    line-height: 32px;
  }
  .contacts {
    position: absolute;
    left: 53px;
    top: 683px;
    margin: 0;
    padding: 0;
    list-style: none;
  }
  .contact {
    display: flex;
    align-items: center;
    height: 32px;
    font-size: 25px;
    white-space: nowrap;
  }
  .contact-icon {
    width: 28px;
    height: 28px;
    margin-right: 11px;
    flex: none;
    background: var(--pink);
  }
</style>
</head>
<body>
<main class="canvas">
  <article class="card">
    <svg class="card-shapes" viewBox="0 0 583 1020" width="583" height="1020" aria-hidden="false">
      <defs>
        <radialGradient id="portraitTone" cx="50%" cy="40%" r="60%">
          <stop offset="0%" stop-color="var(--photo-light)"/>
          <stop offset="100%" stop-color="var(--photo-dark)"/>
        </radialGradient>
      </defs>
      <rect class="card-base" width="583" height="1020" fill="var(--ink)"/>
      <path class="top-band" d="M0,335 C120,205 330,105 583,72 L583,182 C330,192 120,272 0,392 Z" fill="var(--pink)"/>
      <path class="top-band-stripe" d="M0,372 C125,252 335,160 583,145" fill="none" stroke="var(--paper)" stroke-width="9"/>
      <path class="body-panel" d="M0,392 C120,272 330,192 583,182 L583,790 C460,900 260,955 0,905 Z" fill="var(--paper)"/>
      <path class="bottom-band" d="M0,905 C260,955 460,900 583,790 L583,812 C460,930 260,978 0,925 Z" fill="var(--pink)"/>
      <circle class="portrait-ring" cx="411" cy="175" r="140" fill="var(--pink)"/>
      <circle class="portrait" cx="411" cy="175" r="126" fill="url(#portraitTone)" role="img" aria-label="Portrait photo of the card holder"/>
    </svg>

    <h1 class="holder-name">Dorian Fellsmore</h1>
    <p class="roles">Actor, Producer,Vocal Coach<br>Choral Director,Song Writer</p>

    <ul class="contacts">
      <li class="contact">
        <svg class="contact-icon" viewBox="0 0 28 28" aria-label="Phone">
          <rect width="28" height="28" fill="var(--pink)"/>
          <path d="M6 11c0-3 4-5 8-5s8 2 8 5l-3 1-1-2c-2-1-6-1-8 0l-1 2z M8 14h12l1 7H7z" fill="var(--paper)"/>
        </svg>
        (215) 555-0142
      </li>
      <li class="contact">
        <svg class="contact-icon" viewBox="0 0 28 28" aria-label="Fax">
          <rect width="28" height="28" fill="var(--pink)"/>
          <path d="M9 5h10v6H9z M5 12h18v8h-4v3H9v-3H5z" fill="var(--paper)"/>
          <rect x="11" y="17" width="6" height="4" fill="var(--pink)"/>
        </svg>
        (215) 555-0187
      </li>
      <li class="contact">
        <svg class="contact-icon" viewBox="0 0 28 28" aria-label="Email">
          <rect width="28" height="28" fill="var(--pink)"/>
          <rect x="5" y="8" width="18" height="13" fill="none" stroke="var(--paper)" stroke-width="2"/>
          <path d="M5 8l9 8 9-8 M5 21l7-6 M23 21l-7-6" fill="none" stroke="var(--paper)" stroke-width="1.6"/>
        </svg>
        dorianfellsmore@postlane.net
      </li>
      <li class="contact">
        <span class="contact-icon" aria-hidden="true"></span>
        socialpage.net/dorian.fellsmore
      </li>
      <li class="contact">
        <span class="contact-icon" aria-hidden="true"></span>
        @thedf482
      </li>
    </ul>
  </article>
</main>
</body>
</html>
```